Creation of brand identity and website "Tandem K"

I am currently seeking an brand, identity and web design for a new project called Tandem K. This is a brand new concept from scratch and you have free-reign on the whole design process, taking into account my preference below.

Must include the name "Tandem K", or "Tandem K: Or the year I woke Up". Kudos is this forms part of the brands logo

Design that can be easily scaled to potentially include: a blog, timeline and vlogs.

Minimal but effective use of colour (however any colours and combinations permitted

Use of icons/graphics over text wherever possible

Minimal use of frames and borders

I appreciate this is a fairly wide scope so please contact me on marblefinch@postwillow.com with any questions or more information on what the project is.

Target Market(s)

Male and Female 20-40
Blog readers
Selfhelp

Industry/Entity Type

Seeking

Number of Pages Required

1 page

Font styles to use
Serif
Sans Serif

Requirements
Must have
• It is in effect a blog design, so about me section, recent blog / archived posts, reader comments / Q and A section.
• A coded design would be appreciated to make my life easier however I have left the design as uncoded as getting the right design matters more to me and I want to keep the project open to as many designers as possible
Nice to have
• See project description for other details and please ask if you need anything else :)
Should not have
• Mustn't be cluttered or feel fussy
• Promote icons over text
• Frames / multiple borders

```html
<!DOCTYPE html>
<html lang="en">
<head>
<meta charset="utf-8">
<title>Tandem K</title>
<link href="https://fonts.googleapis.com/css2?family=Oswald:wght@400;500&family=Lato:ital,wght@0,400;0,700;1,700&display=swap" rel="stylesheet">
<style>
:root{
  --navy:#213559;
  --gold:#f4bb22;
  --text:#444;
  --line:#dcdcdc;
  --page:#fbfbfb;
  --red:#e2533f;
  --cyan:#2aa6dc;
  --blue:#3b5ea8;
}
*{box-sizing:border-box;margin:0;padding:0}
html,body{width:700px;height:1200px;overflow:hidden}
body{position:relative;background:var(--page);font-family:'Lato',sans-serif;color:var(--text)}
.abs{position:absolute}
.head{font-family:'Oswald',sans-serif;font-weight:400}

/* header */
.site-header{left:0;top:0;width:700px;height:40px;background:#fff;z-index:2}
.logo{left:76px;top:6px;font-family:'Oswald',sans-serif;font-size:19px;color:var(--navy);font-weight:500}
.nav a{position:absolute;top:0;height:40px;line-height:38px;font-family:'Oswald',sans-serif;font-size:10px;color:var(--navy);text-decoration:none;letter-spacing:.2px}
.nav a.active{background:var(--navy);color:#fff;border-bottom:3px solid var(--gold);padding:0 9px}

/* hero */
.hero-bg{left:0;top:40px;width:700px;height:210px;background:linear-gradient(90deg,#eef0ee 0%,#e6e9e6 45%,#dfe3df 70%,#eceeec 100%)}
.portrait{left:76px;top:68px;width:157px;height:157px;border:3px solid #d6d6d6;background:linear-gradient(160deg,#8fa4b4,#c9b8a6 55%,#8ca0c0)}
.hero-title{left:255px;top:64px;font-size:15px;color:var(--navy)}
.hero-text{left:255px;top:98px;width:368px;font-size:8.4px;line-height:12.3px;color:#444}
.btn{display:block;background:var(--navy);color:#fff;font-family:'Oswald',sans-serif;font-size:9px;text-align:center;text-decoration:none}
.hero-btn{left:255px;top:199px;width:59px;height:24px;line-height:24px;font-size:10px}

/* posts */
.section-bar{left:76px;top:274px;width:361px;height:19px;background:var(--navy);color:#fff;font-size:11.5px;line-height:19px;padding-left:9px}
.section-bar svg{position:absolute;right:6px;top:3px}
.post{left:76px;width:361px;height:145px;background:#fff;border:1px solid var(--line)}
.post .thumb{position:absolute;left:8px;top:8px;width:137px;height:124px;border:3px solid #e8e8e8}
.post h2{position:absolute;left:154px;top:8px;font-size:10.6px;color:var(--navy);font-family:'Oswald',sans-serif;font-weight:400}
.post .rule{position:absolute;left:154px;top:27px;width:197px;border-top:1px solid var(--line)}
.meta{position:absolute;left:154px;top:35px;font-size:7.3px;color:#444;display:flex;align-items:center}
.meta .sep{display:inline-block;width:1px;height:14px;background:#888;margin:0 6px}
.meta svg{margin-right:5px}
.excerpt{position:absolute;left:154px;top:54px;width:200px;font-size:7px;line-height:12px;color:#555}
.count{position:absolute;top:98px;width:25px;height:16px;border:1px solid;font-size:7px;text-align:center;line-height:14px;background:#fff}
.count.c1{left:154px;border-color:var(--blue);color:var(--blue)}
.count.c2{left:191px;border-color:var(--red);color:var(--red)}
.count.c3{left:229px;border-color:var(--cyan);color:var(--cyan)}
.count.c4{left:266px;border-color:#888;color:#444}
.chip{position:absolute;top:118px;width:25px;height:11px;font-size:6px;line-height:9px;text-align:center;border:1px solid #ccc;color:#555;background:#fafafa}
.chip.c1{left:154px;background:var(--blue);color:#fff;border-color:var(--blue)}
.chip.c2{left:191px;color:var(--red)}
.chip.c3{left:229px;color:var(--navy)}
.chip.c4{left:266px}
.share{position:absolute;left:312px;top:96px;font-size:7px;color:#555;display:flex;align-items:center;gap:4px}
.post .btn{position:absolute;left:293px;top:113px;width:57px;height:20px;line-height:20px;border-radius:2px}
.load-more{left:76px;top:1126px;width:361px;height:25px;background:var(--gold);color:var(--navy);font-size:8.5px;line-height:25px;display:flex;justify-content:center;align-items:center;gap:6px}

/* sidebar */
.box{left:451px;width:172px;background:#fff;border:1px solid var(--line)}
.box h3{font-family:'Oswald',sans-serif;font-weight:400;font-size:10.5px;color:var(--navy);margin:5px 0 0 8px}
.newsletter{top:274px;height:86px}
.newsletter .field{position:absolute;left:7px;top:26px;width:157px;height:22px;border:1px solid var(--line);font-size:7px;color:#999;line-height:20px;padding-left:6px}
.newsletter .btn{position:absolute;left:7px;top:57px;width:58px;height:21px;line-height:21px;font-size:8px}
.popular{top:377px;height:233px}
.popular .title{height:20px;background:#6b6b6b;color:#fff;font-size:10.5px;text-align:center;line-height:20px}
.tabs{display:flex;height:20px;font-family:'Oswald',sans-serif;font-size:8px;background:var(--gold);color:var(--navy)}
.tabs span{line-height:20px;text-align:center}
.tabs .on{background:var(--navy);color:#fff;width:53px;position:relative}
.tabs .on::after{content:"";position:absolute;left:22px;bottom:-5px;border:5px solid transparent;border-bottom:0;border-top-color:var(--navy)}
.pop-item{position:absolute;left:8px;width:156px;display:flex;gap:11px}
.pop-item .pic{width:46px;height:45px;flex:none}
.pop-item p{font-size:7.3px;font-style:italic;font-weight:700;line-height:10.6px;color:#333;padding-top:6px}
.view-all{position:absolute;right:8px;bottom:7px;font-size:7.5px;color:var(--navy);font-family:'Oswald',sans-serif;text-decoration:underline}
.follow{top:628px;height:64px;border-top:4px solid #e4e4e4;border-bottom:4px solid #e4e4e4}
.follow .icons{position:absolute;left:8px;top:30px;display:flex;gap:12px}
.follow .icons span{width:21px;height:21px;display:block}
.archives{top:710px;height:138px}
.archives ul{list-style:none;margin:6px 7px 0}
.archives li{font-size:7.3px;font-weight:700;color:#333;height:16px;line-height:15px;border-bottom:1px solid #e8e8e8;padding-left:2px}
.tags{top:866px;height:107px}
.tag-list{position:absolute;left:8px;top:26px;width:160px;display:flex;flex-wrap:wrap;gap:8px 4px}
.tag-list span{background:var(--gold);color:var(--navy);font-family:'Oswald',sans-serif;font-size:9.5px;height:19px;line-height:19px;text-align:center}
.ad{left:451px;top:990px;width:172px;height:116px;background:linear-gradient(180deg,#7a4a3a 0%,#c07a4a 35%,#3a2a28 70%,#1a1414 100%)}

.site-footer{left:0;top:1173px;width:700px;height:27px;background:var(--navy);color:#fff;font-family:'Oswald',sans-serif;font-size:7.5px;text-align:center;line-height:27px}
</style>
</head>
<body>

<header class="site-header abs">
  <div class="logo abs">Tandem K</div>
  <nav class="nav">
    <a class="active" href="#" style="left:325px">About Me</a>
    <a href="#" style="left:401px">Recent Blog</a>
    <a href="#" style="left:479px">Reader Comments</a>
    <a href="#" style="left:580px">Contact Us</a>
  </nav>
</header>

<section class="hero-bg abs" role="img" aria-label="Faded photo of a couple with a bicycle in a meadow"></section>
<div class="portrait abs" role="img" aria-label="Portrait photo of the blog author"></div>
<h1 class="hero-title head abs">About Me</h1>
<p class="hero-text abs">Lorem ipsum dolor sit amet, consectetuer adipiscing elit, sed diam nonummy nibh euismod alme tincidunt ut laoreet dolore magna aliquam erat volutpat. Ut wisi enim ad minim veniam, quis dol nostrud exerci tation ullamcorper suscipit lobortis nisl ut aliquip ex ea commodo consequat list Duis autem vel eum iriure dolor in hendrerit in vulputate velit esse molestie consequat, vel alm illum dolore eu feugiat nulla facilisis at vero eros et accumsan et iusto odio dignissim qui blandit illum dolore eu feugiat nulla facilisis at vero eros et accumsan et iusto odio dignissim qui blandit praesent luptatum zzril delenit augue duis dolore te feugait nulla facilisi.</p>
<a class="btn hero-btn abs" href="#">Read More</a>

<div class="section-bar abs head">Recent Blog Posts
  <svg width="13" height="13" viewBox="0 0 13 13"><rect x="1" y="1" width="10" height="11" fill="none" stroke="#f4bb22" stroke-width="1.3"/><path d="M3 4h6M3 6.5h6M3 9h4" stroke="#f4bb22"/></svg>
</div>

<article class="post abs" style="top:300px">
  <div class="thumb" role="img" aria-label="Photo of a woman stretching her arms towards the sun" style="background:linear-gradient(160deg,#3a78c8,#9ec6ea 45%,#d8a0c8)"></div>
  <h2>Lorem ipsum dolor sit amet consecit dolor</h2><div class="rule"></div>
  <div class="meta"><svg width="8" height="8"><rect width="8" height="8" rx="1" fill="#f4bb22"/></svg>June 18, 2016<span class="sep"></span><svg width="9" height="8"><ellipse cx="4.5" cy="3.5" rx="4.5" ry="3.5" fill="#f4bb22"/></svg>No Comments</div>
  <p class="excerpt">Lorem ipsum dolor sit amet, consecit adipiscing elit, sed do eiusmod tempor incidimen labore n dolorme laboris ni ut ullamco Neque porro quisquam est, qui dolorem ipsum</p>
  <span class="count c1">560</span><span class="count c2">36</span><span class="count c3">456</span><span class="count c4">1066</span>
  <span class="chip c1">Like</span><span class="chip c2">Plus</span><span class="chip c3">Post</span><span class="chip c4">Email</span>
  <div class="share">Share <svg width="11" height="9"><path d="M1 8 Q2 3 7 3 V0 L11 4 7 8 V5 Q3 5 1 8Z" fill="#f4bb22"/></svg></div>
  <a class="btn" href="#">Read More</a>
</article>

<article class="post abs" style="top:464px">
  <div class="thumb" role="img" aria-label="Photo of a woman with pink hair on a beach" style="background:linear-gradient(160deg,#cfe0e8,#e8cfc0 50%,#c89a8a)"></div>
  <h2>Lorem ipsum dolor sit amet consecit dolor</h2><div class="rule"></div>
  <div class="meta"><svg width="8" height="8"><rect width="8" height="8" rx="1" fill="#f4bb22"/></svg>June 22, 2016<span class="sep"></span><svg width="9" height="8"><ellipse cx="4.5" cy="3.5" rx="4.5" ry="3.5" fill="#f4bb22"/></svg>No Comments</div>
  <p class="excerpt">Lorem ipsum dolor sit amet, consecit adipiscing elit, sed do eiusmod tempor incidimen labore n dolorme laboris ni ut ullamco Neque porro quisquam est, qui dolorem ipsum</p>
  <span class="count c1">560</span><span class="count c2">36</span><span class="count c3">456</span><span class="count c4">1066</span>
  <span class="chip c1">Like</span><span class="chip c2">Plus</span><span class="chip c3">Post</span><span class="chip c4">Email</span>
  <div class="share">Share <svg width="11" height="9"><path d="M1 8 Q2 3 7 3 V0 L11 4 7 8 V5 Q3 5 1 8Z" fill="#f4bb22"/></svg></div>
  <a class="btn" href="#">Read More</a>
</article>

<article class="post abs" style="top:629px">
  <div class="thumb" role="img" aria-label="Black and white photo of a smiling couple" style="background:linear-gradient(160deg,#2a2a2a,#8a8a8a 55%,#d0d0d0)"></div>
  <h2>Lorem ipsum dolor sit amet consecit dolor</h2><div class="rule"></div>
  <div class="meta"><svg width="8" height="8"><rect width="8" height="8" rx="1" fill="#f4bb22"/></svg>June 26, 2016<span class="sep"></span><svg width="9" height="8"><ellipse cx="4.5" cy="3.5" rx="4.5" ry="3.5" fill="#f4bb22"/></svg>No Comments</div>
  <p class="excerpt">Lorem ipsum dolor sit amet, consecit adipiscing elit, sed do eiusmod tempor incidimen labore n dolorme laboris ni ut ullamco Neque porro quisquam est, qui dolorem ipsum</p>
  <span class="count c1">560</span><span class="count c2">36</span><span class="count c3">456</span><span class="count c4">1066</span>
  <span class="chip c1">Like</span><span class="chip c2">Plus</span><span class="chip c3">Post</span><span class="chip c4">Email</span>
  <div class="share">Share <svg width="11" height="9"><path d="M1 8 Q2 3 7 3 V0 L11 4 7 8 V5 Q3 5 1 8Z" fill="#f4bb22"/></svg></div>
  <a class="btn" href="#">Read More</a>
</article>

<article class="post abs" style="top:794px">
  <div class="thumb" role="img" aria-label="Photo of a family playing in a poppy field" style="background:linear-gradient(180deg,#9cc8e8,#d8e8f0 45%,#7aa050 75%,#c84a2a)"></div>
  <h2>Lorem ipsum dolor sit amet consecit dolor</h2><div class="rule"></div>
  <div class="meta"><svg width="8" height="8"><rect width="8" height="8" rx="1" fill="#f4bb22"/></svg>June 30, 2016<span class="sep"></span><svg width="9" height="8"><ellipse cx="4.5" cy="3.5" rx="4.5" ry="3.5" fill="#f4bb22"/></svg>No Comments</div>
  <p class="excerpt">Lorem ipsum dolor sit amet, consecit adipiscing elit, sed do eiusmod tempor incidimen labore n dolorme laboris ni ut ullamco Neque porro quisquam est, qui dolorem ipsum</p>
  <span class="count c1">560</span><span class="count c2">36</span><span class="count c3">456</span><span class="count c4">1066</span>
  <span class="chip c1">Like</span><span class="chip c2">Plus</span><span class="chip c3">Post</span><span class="chip c4">Email</span>
  <div class="share">Share <svg width="11" height="9"><path d="M1 8 Q2 3 7 3 V0 L11 4 7 8 V5 Q3 5 1 8Z" fill="#f4bb22"/></svg></div>
  <a class="btn" href="#">Read More</a>
</article>

<article class="post abs" style="top:960px">
  <div class="thumb" role="img" aria-label="Photo of a man with open arms on a sailing boat" style="background:linear-gradient(180deg,#a8c8e0,#e0e8ee 45%,#3a6a98 70%,#f0f0f0)"></div>
  <h2>Lorem ipsum dolor sit amet consecit dolor</h2><div class="rule"></div>
  <div class="meta"><svg width="8" height="8"><rect width="8" height="8" rx="1" fill="#f4bb22"/></svg>July 01, 2016<span class="sep"></span><svg width="9" height="8"><ellipse cx="4.5" cy="3.5" rx="4.5" ry="3.5" fill="#f4bb22"/></svg>No Comments</div>
  <p class="excerpt">Lorem ipsum dolor sit amet, consecit adipiscing elit, sed do eiusmod tempor incidimen labore n dolorme laboris ni ut ullamco Neque porro quisquam est, qui dolorem ipsum</p>
  <span class="count c1">560</span><span class="count c2">36</span><span class="count c3">456</span><span class="count c4">1066</span>
  <span class="chip c1">Like</span><span class="chip c2">Plus</span><span class="chip c3">Post</span><span class="chip c4">Email</span>
  <div class="share">Share <svg width="11" height="9"><path d="M1 8 Q2 3 7 3 V0 L11 4 7 8 V5 Q3 5 1 8Z" fill="#f4bb22"/></svg></div>
  <a class="btn" href="#">Read More</a>
</article>

<div class="load-more abs head">
  <svg width="11" height="11" viewBox="0 0 11 11"><g stroke="#213559" stroke-width="1.4" stroke-linecap="round"><path d="M5.5 1v2M5.5 8v2M1 5.5h2M8 5.5h2M2.3 2.3l1.4 1.4M7.3 7.3l1.4 1.4M2.3 8.7l1.4-1.4M7.3 3.7l1.4-1.4"/></g></svg>
  Load More Blogs
</div>

<aside>
  <div class="box newsletter abs">
    <h3>Sign Up For Free Newsletter</h3>
    <div class="field">Enter Your Email Address</div>
    <a class="btn" href="#">SUBSCRIBE</a>
  </div>

  <div class="box popular abs">
    <div class="title head">Popular</div>
    <div class="tabs"><span class="on">Page Views</span><span style="width:66px">Social Shares#</span><span style="width:51px">Comments</span></div>
    <div class="pop-item" style="top:60px"><div class="pic" role="img" aria-label="Photo of a woman in a green field" style="background:linear-gradient(160deg,#e8f0d8,#6a9a3a)"></div><p>Lorem ipsum dolor sit ame consectetuer adipiscing Dolor sit almet</p></div>
    <div class="pop-item" style="top:111px"><div class="pic" role="img" aria-label="Photo of a woman in a white dress" style="background:linear-gradient(160deg,#f0f0e8,#8aa86a)"></div><p>Lorem ipsum dolor sit ame consectetuer adipiscing Dolor sit almet</p></div>
    <div class="pop-item" style="top:162px"><div class="pic" role="img" aria-label="Photo of a smiling man" style="background:linear-gradient(160deg,#d8d8d8,#8a6a5a)"></div><p style="padding-top:12px">Lorem ipsum dolor sit ame consectetuer adipiscing</p></div>
    <span class="view-all">View All &gt;&gt;</span>
  </div>

  <div class="box follow abs">
    <h3>Follow Us</h3>
    <div class="icons">
      <span aria-label="Social profile one" style="background:#1e5a9e"></span>
      <span aria-label="Social profile two" style="background:#d6402c"></span>
      <span aria-label="Social profile three" style="background:#2aa6dc"></span>
      <span aria-label="Social profile four" style="background:#c4302b"></span>
      <span aria-label="Social profile five" style="background:#1f5f8b"></span>
    </div>
  </div>

  <div class="box archives abs">
    <h3>Archives</h3>
    <ul>
      <li>July 2016</li><li>June 2016</li><li>May 2016</li><li>April 2016</li><li>March 2016</li><li>February 2016</li><li style="border:0">January 2016</li>
    </ul>
  </div>

  <div class="box tags abs">
    <h3>Popular Tags</h3>
    <div class="tag-list">
      <span style="width:34px">SIT</span><span style="width:51px">DOLOR</span><span style="width:66px">ALMETSIT</span>
      <span style="width:48px">DOLOR</span><span style="width:50px">ELIT</span><span style="width:42px">SIT</span>
      <span style="width:40px">ELIT</span><span style="width:50px">ALMETS</span>
    </div>
  </div>

  <div class="ad abs" role="img" aria-label="Advertisement photo of an off-road vehicle at sunset"></div>
</aside>

<footer class="site-footer abs">© 2016 Tandem K. All Rights Reserved.</footer>

</body>
</html>
```